Luxury Wine Label for New Startup Winery

We need a wine label for our new winery startup. We have worked with a local designer but do not feel the resulting label / logo have the elevation required to present our brand as a luxury wine. Our winery is called "Quailbrook Vineyards" and we are focused on extremely high quality hand crafted artisan and estate wines from the Pacific Northwest.
We would like to see designs that utilize a tree line, or other imagery that represents the "Quailbrook" part of our company name. Another interesting feature could be wood grain.
A logo will be required based on your design so please design with this in mind:
This logo should be consistent with the wine bottle label design, and should be representative of our high end exclusive wine while giving a sense of place (Oregon/ Pacific Northwest.)
I will supply an image of the design we received from our local designer, PLEASE NOTE: in general we do like wood grain and tree line concepts but feel the execution was poorly done.
ATTN: Logo design should be suitable for use on: Bottles (Red wine/rose/white wine), Bussiness cards, vehicle signage, business signage, etc
P.S.:
If you have a design that is not outside the box we are still interested in seeing it.
Label is for a burgundy style bottle with a label height of 3.5 - 4" and a width of 3.5-4"
any label <= 4"x4" and >=3.5"x3.5" will be acceptable:
HOWEVER Width should be greater than or equal to height due to the bottle format
Target Market(s)
Wine enthusiasts with adequate discretionary budgets to afford $100 bottles of wine.
Industry/Entity Type
Wine / Winery
Requirements
Must have
- A sense of luxury, a feel of exclusivity, and a theme consistent with our product and brand name
Nice to have
- Tree line, wood grain or other wood themes. Serif fonts
Should not have
- anything cheesy, off topic, hard to read script fonts or anything that makes the label hard to read from a few feet away or too busy

```html
<!DOCTYPE html>
<html lang="en">
<head>
<meta charset="utf-8">
<title>Quailbrook Vineyards – Rosé Label</title>
<link rel="stylesheet" href="https://fonts.googleapis.com/css2?family=Cinzel:wght@600;700&family=Oswald:wght@400&display=swap">
<style>
  :root {
    --page-bg: #ffffff;
    --label-top: #fcecea;
    --label-mid: #fbe4e1;
    --tree-light: rgba(240, 150, 145, 0);
    --tree-mid: #f2a19c;
    --tree-deep: #ec7a74;
    --brand-brown: #3d2220;
    --region-orange: #e0743a;
    --varietal-red: #e05a52;
    --footer-text: #ffffff;
  }
  * { margin: 0; padding: 0; box-sizing: border-box; }
  html, body {
    width: 1200px;
    height: 1200px;
    overflow: hidden;
    background: var(--page-bg);
  }
  .canvas {
    position: relative;
    width: 1200px;
    height: 1200px;
  }
  .label {
    position: absolute;
    left: 100px;
    top: 238px;
    width: 1000px;
    height: 723px;
    border-radius: 14px;
    overflow: hidden;
    background: linear-gradient(180deg, var(--label-top) 0%, var(--label-mid) 50%, var(--label-mid) 100%);
  }
  .treeline {
    position: absolute;
    left: 0;
    top: 330px;
    width: 1000px;
    height: 393px;
  }
  .brand-mark {
    position: absolute;
    left: 50%;
    top: 60px;
    width: 72px;
    height: 72px;
    margin-left: -36px;
    background: var(--brand-brown);
  }
  .brand-name {
    position: absolute;
    top: 148px;
    width: 100%;
    text-align: center;
    font-family: "Cinzel", serif;
    font-weight: 700;
    font-size: 30px;
    line-height: 33px;
    letter-spacing: 2px;
    color: var(--brand-brown);
  }
  .region {
    position: absolute;
    top: 220px;
    width: 100%;
    text-align: center;
    font-family: "Oswald", sans-serif;
    font-size: 18px;
    letter-spacing: 1.5px;
    color: var(--region-orange);
  }
  .varietal {
    position: absolute;
    top: 298px;
    width: 100%;
    text-align: center;
    font-family: "Cinzel", serif;
    font-weight: 700;
    font-size: 44px;
    letter-spacing: 3px;
    color: var(--varietal-red);
  }
  .details {
    position: absolute;
    top: 652px;
    width: 100%;
    text-align: center;
    font-family: "Oswald", sans-serif;
    font-size: 15px;
    color: var(--footer-text);
    letter-spacing: 0.5px;
  }
  .details .vintage { font-size: 22px; margin: 0 6px; }
  .details .divider { margin: 0 10px; }
</style>
</head>
<body>
  <main class="canvas">
    <section class="label">
      <svg class="treeline" viewBox="0 0 1000 393" role="img" aria-label="Misty coral tree line of evergreen forest across the lower part of the label">
        <defs>
          <linearGradient id="forestFade" x1="0" y1="0" x2="0" y2="1">
            <stop offset="0" stop-color="var(--tree-light)"/>
            <stop offset="0.3" stop-color="var(--tree-mid)" stop-opacity="0.7"/>
            <stop offset="0.6" stop-color="var(--tree-deep)" stop-opacity="0.85"/>
            <stop offset="1" stop-color="var(--tree-deep)"/>
          </linearGradient>
        </defs>
        <rect x="0" y="0" width="1000" height="393" fill="url(#forestFade)"/>
      </svg>

      <div class="brand-mark" aria-hidden="true"></div>
      <h1 class="brand-name">Quailbrook<br>Vineyards</h1>
      <p class="region">WILLAMETTE VALLEY, OREGON</p>
      <h2 class="varietal">Rosé</h2>
      <p class="details">750 ml<span class="divider">/</span><span class="vintage">2024</span><span class="divider">/</span>13% Alc. Vol.</p>
    </section>
  </main>
</body>
</html>
```